Government Contracting business needs a website design.

Pellworth & Quine, LLC is a minority owned Service Disabled Veteran Owned Small Business (SDVOSB) that provides Strategic Planning, Public Health Emergency Response, and Data Management Solutions for Federal Civilian and Defense Agencies. We have over 20 years of experience helping health and defense agencies develop concept of operations, deploy assets and personnel in Hot Zones around the world, and deliver goods and services all of the globe.

We are a leader in the field of Data Management. We help our customers develop cloud migration and disaster recovery strategies. We are experts with database management, data replication, queries, consolidation, and records management.

We are looking for a very nice and simple website designs that states clearly what we do as a company and that is easy for our customers to follow. We would like to have some moving pictures that are base on our expertise. We want the website to be easy to use and have the scroll down features that keeps things all on the same page when clicking on the menu. I attached a document with what we need on the website. I will also attach our logo. We want it to look simple clean and very professional.

Target Market(s)

Government Contracting, Management Consulting, Health

Industry/Entity Type

Government

Coding

Coded - Design and coding required

Number of Pages Required

1 page

Font styles to use
Serif

Requirements
Must have
• Very nice picture slides that speaks to our capabilities in Disaster Response, Strategic Planning, and Database Management. Slick look and design. Make sure SDVOSB Logo is right at the beginning of website as our customers is looking for that certification. Very nice colors that blend well with our logo.
Nice to have
• Very nice and slick colors that blends well with logo.
Should not have
• Basic website design that are weary on the eye. No bright colors, just simple colors that looks good with logo.

```html
<!DOCTYPE html>
<html lang="en">
<head>
<meta charset="utf-8">
<title>Pellworth &amp; Quine, LLC</title>
<link rel="stylesheet" href="https://fonts.googleapis.com/css2?family=Lora:wght@400;700&family=Lato:wght@400;700&display=swap">
<style>
:root{
  --teal-dark:#2f5668;
  --teal-mid:#3f6b7c;
  --teal-light:#a9d0cc;
  --teal-pale:#dcefee;
  --ink:#2c2c2c;
  --text:#3a3a3a;
  --grey-card:#474747;
  --white:#ffffff;
}
*{margin:0;padding:0;box-sizing:border-box}
html,body{width:1200px;height:3442px;overflow:hidden;background:var(--white)}
body{position:relative;font-family:"Lato",Arial,sans-serif;color:var(--text)}
.abs{position:absolute}
.backdrop{position:absolute;left:0;top:0;width:1200px;height:3442px}
.serif{font-family:"Lora",Georgia,serif}

.brand{left:96px;top:26px;font-family:"Lora",Georgia,serif;font-size:30px;color:var(--white);display:flex;align-items:center;gap:12px}
.brand .mark{width:22px;height:22px;background:var(--white)}
.nav{top:46px;left:536px;display:flex;gap:32px;font-size:14px;font-weight:700;color:var(--ink);white-space:nowrap}
.badge{left:1026px;top:22px;width:74px;height:74px;border-radius:50%;background:var(--white);border:5px solid #c8d2e6}

.hero-title{left:96px;top:222px;font-family:"Lora",Georgia,serif;font-weight:700;font-size:50px;color:var(--teal-dark)}
.hero-copy{left:98px;top:305px;width:440px;font-size:15px;line-height:1.6;color:var(--ink)}
.btn{display:inline-flex;align-items:center;justify-content:center;width:130px;height:50px;border-radius:25px;background:var(--teal-dark);color:var(--white);font-size:14px;box-shadow:0 4px 10px rgba(0,0,0,.25)}
.btn-outline{background:transparent;border:2px solid var(--white);box-shadow:none}
.dots{left:98px;top:486px;display:flex;gap:6px}
.dots span{width:16px;height:16px;border-radius:50%;background:#dedede}
.dots span:first-child{background:var(--teal-dark)}
.servers{left:690px;top:190px;width:420px;height:320px;border-radius:8px;background:linear-gradient(135deg,#c9ccce,#6e7478 55%,#2b2f33);box-shadow:0 0 30px rgba(255,255,255,.6)}

.about-art{left:46px;top:610px;width:400px;height:420px;border-radius:20px;background:radial-gradient(circle at 50% 60%,#d7f0ef,#a9d0cc 70%)}
.section-title{font-family:"Lora",Georgia,serif;font-weight:700;color:var(--teal-dark)}
.about-title{left:539px;top:695px;font-size:42px}
.about-copy{left:539px;top:768px;width:562px;font-size:15px;line-height:1.7;text-align:justify;color:var(--ink)}
.about-copy p+p{margin-top:12px}

.core-photo{left:0;top:1245px;width:1200px;height:730px;background:linear-gradient(180deg,#f6f6f6,#ececec 60%,#f2f2f2)}
.core-title{left:0;top:1285px;width:1200px;text-align:center;font-size:42px}
.core-copy{left:98px;top:1356px;width:1004px;text-align:center;font-size:15px;line-height:1.65;color:var(--ink)}
.card{width:330px;height:310px;color:var(--white);text-align:center}
.card-shape{position:absolute;left:0;top:0}
.card-body{position:absolute;left:30px;top:40px;width:270px}
.card-icon{display:block;margin:0 auto 14px}
.card h3{font-family:"Lora",Georgia,serif;font-weight:700;font-size:20px;line-height:1.3;margin-bottom:12px;white-space:nowrap}
.card p{font-size:12.5px;line-height:1.6;padding:0 14px}
.card .more{display:block;margin-top:14px;font-size:15px;font-weight:700}
.card .chev{display:block;margin:12px auto 0}

.lead-title{left:98px;top:2045px;font-size:38px;display:flex;align-items:center;gap:26px}
.lead-name{left:98px;top:2116px;font-family:"Lora",Georgia,serif;font-weight:700;font-size:20px;color:var(--teal-dark)}
.lead-role{left:98px;top:2146px;font-size:16px;color:var(--ink)}
.lead-copy{left:98px;top:2182px;width:600px;font-size:14.5px;line-height:1.7;color:var(--ink)}
.lead-copy p+p{margin-top:11px}
.lead-quote{left:98px;top:2490px;font-family:"Lora",Georgia,serif;font-size:20px;color:var(--teal-dark)}
.portrait{left:860px;top:2080px;width:300px;height:350px;border-radius:24px;background:linear-gradient(180deg,#bcdcd8,#8fbfba)}

.join-title{left:0;top:2750px;width:1200px;text-align:center;font-size:40px;color:var(--white)}
.join-copy{left:98px;top:2826px;width:1004px;text-align:center;font-size:14.5px;line-height:1.7;color:var(--white)}
.join-copy p+p{margin-top:18px}

.foot-brand{left:800px;top:3236px;font-family:"Lora",Georgia,serif;font-size:32px;color:var(--teal-dark);display:flex;align-items:center;gap:14px}
.foot-brand .mark{width:24px;height:24px;background:var(--teal-dark)}
.foot-nav{left:604px;top:3336px;display:flex;gap:34px;font-size:15px;font-weight:700;color:var(--ink)}
.foot-rule{left:540px;top:3376px;width:560px;height:2px;background:var(--ink)}
.copyright{left:722px;top:3398px;font-size:14px;font-weight:700;color:var(--ink)}
</style>
</head>
<body>

<svg class="backdrop" width="1200" height="3442" viewBox="0 0 1200 3442" aria-hidden="true">
  <defs>
    <linearGradient id="joinShade" x1="0" y1="0" x2="1" y2="1">
      <stop offset="0" stop-color="#3d6678"/><stop offset="1" stop-color="#2c5163"/>
    </linearGradient>
  </defs>
  <path d="M0 0H600C430 40 240 70 0 175Z" fill="var(--teal-dark)"/>
  <path d="M870 0H1200V592Q1150 582 1100 560L730 415Q650 385 700 320L910 55Z" fill="var(--teal-dark)"/>
  <path d="M0 575Q60 560 115 600L470 842Q505 872 470 902L115 1148Q60 1185 0 1172Z" fill="var(--teal-light)"/>
  <path d="M0 1230Q300 1290 700 1250T1200 1220" fill="none" stroke="var(--teal-dark)" stroke-width="4"/>
  <path d="M0 1960Q500 2000 900 1880T1200 1822" fill="none" stroke="var(--teal-dark)" stroke-width="4"/>
  <path d="M770 2228Q745 2248 770 2268L955 2425H1200V2090L1060 2030Q1035 2018 1010 2035Z" fill="var(--teal-light)"/>
  <path d="M0 2740Q40 2670 160 2670H1200V3170Q900 3150 600 3210T0 3215Z" fill="var(--teal-dark)"/>
  <path d="M0 2745Q40 2680 160 2680H1200V3165Q900 3145 600 3205T0 3210Z" fill="url(#joinShade)"/>
</svg>

<header>
  <div class="abs brand"><span class="mark"></span>Pellworth &amp; Quine</div>
  <nav class="abs nav"><span>HOME</span><span>ABOUT</span><span>SERVICES</span><span>WHY HIRE US?</span><span>CONTACT</span></nav>
  <div class="abs badge" role="img" aria-label="Veteran-owned business certification badge"></div>
</header>

<section class="hero">
  <h1 class="abs hero-title">Pellworth Quine</h1>
  <p class="abs hero-copy">Nemo enim ipsam voluptatem quia voluptas sit aspernatur aut odit aut fugit, sed quia consequuntur magni dolores.</p>
  <a class="abs btn" style="left:98px;top:396px">Read More</a>
  <div class="abs dots"><span></span><span></span><span></span><span></span><span></span></div>
  <div class="abs servers" role="img" aria-label="Rack of data center servers"></div>
</section>

<section class="about">
  <div class="abs about-art" role="img" aria-label="Illustration of a businessman surrounded by charts, documents and finance icons"></div>
  <h2 class="abs section-title about-title">About Us:</h2>
  <div class="abs about-copy">
    <p>Pellworth &amp; Quine, LLC is a minority owned Service Disabled Veteran Owned Small Business (SDVOSB) that provides Strategic Planning, Public Health Emergency Response, and Data Management Solutions for Federal Civilian and Defense Agencies. We have over 20 years of experience helping health and defense agencies develop concept of operations, deploy assets and personnel in Hot Zones around the world, and deliver goods and services all of the globe.</p>
    <p>We are a leader in the field of Data Management. We help our customers develop cloud migration and disaster recovery strategies. We are experts with database management, data replication, queries, consolidation, and records management.</p>
  </div>
  <a class="abs btn" style="left:539px;top:1027px">Read More</a>
</section>

<section class="core">
  <div class="abs core-photo" role="img" aria-label="Faded photo of a team working in an office"></div>
  <h2 class="abs section-title core-title">Core Capabilities</h2>
  <p class="abs core-copy">We have over 20 years of experience helping health and defense agencies develop concept of operations, deploy assets and personnel in Hot Zones around the world, and deliver goods and services all of the globe.</p>

  <div class="abs card" style="left:94px;top:1450px">
    <svg class="card-shape" width="330" height="310" viewBox="0 0 330 310" aria-hidden="true">
      <path d="M90 14Q108 4 128 4H212Q232 4 250 14L318 136Q328 155 318 174L250 296Q232 306 212 306H128Q108 306 90 296L12 174Q2 155 12 136Z" fill="#7b7b7b" opacity=".55"/>
      <path d="M82 10Q100 0 120 0H204Q224 0 242 10L310 132Q320 151 310 170L242 292Q224 302 204 302H120Q100 302 82 292L10 170Q0 151 10 132Z" fill="var(--grey-card)"/>
    </svg>
    <div class="card-body">
      <svg class="card-icon" width="54" height="48" viewBox="0 0 54 48" fill="none" stroke="#fff" stroke-width="3" aria-hidden="true"><rect x="3" y="3" width="30" height="22" rx="4"/><path d="M10 25V33L18 25"/><path d="M38 15H47Q51 15 51 19V34Q51 38 47 38H44V45L37 38H24Q20 38 20 34V30"/><path d="M12 16L17 11 22 16M17 11V20"/></svg>
      <h3>Disaster Response</h3>
      <p>Providing cutting edge IT Solutions that help DoD and the VA to tackle various health problems.</p>
      <span class="more">Read More</span>
      <svg class="chev" width="18" height="16" viewBox="0 0 18 16" fill="none" stroke="#fff" stroke-width="2" aria-hidden="true"><path d="M3 2L9 7 15 2M3 9L9 14 15 9"/></svg>
    </div>
  </div>

  <div class="abs card" style="left:435px;top:1450px">
    <svg class="card-shape" width="330" height="310" viewBox="0 0 330 310" aria-hidden="true">
      <path d="M90 14Q108 4 128 4H212Q232 4 250 14L318 136Q328 155 318 174L250 296Q232 306 212 306H128Q108 306 90 296L12 174Q2 155 12 136Z" fill="#7b7b7b" opacity=".55"/>
      <path d="M82 10Q100 0 120 0H204Q224 0 242 10L310 132Q320 151 310 170L242 292Q224 302 204 302H120Q100 302 82 292L10 170Q0 151 10 132Z" fill="var(--teal-dark)"/>
    </svg>
    <div class="card-body">
      <svg class="card-icon" width="54" height="48" viewBox="0 0 54 48" fill="none" stroke="#fff" stroke-width="3" aria-hidden="true"><rect x="3" y="3" width="30" height="22" rx="4"/><path d="M10 25V33L18 25"/><path d="M38 15H47Q51 15 51 19V34Q51 38 47 38H44V45L37 38H24Q20 38 20 34V30"/><path d="M12 16L17 11 22 16M17 11V20"/></svg>
      <h3>Strategic Planning</h3>
      <p>Providing cutting edge IT Solutions that help DoD and the VA to tackle various health problems.</p>
      <span class="more">Read More</span>
      <svg class="chev" width="18" height="16" viewBox="0 0 18 16" fill="none" stroke="#fff" stroke-width="2" aria-hidden="true"><path d="M3 2L9 7 15 2M3 9L9 14 15 9"/></svg>
    </div>
  </div>

  <div class="abs card" style="left:775px;top:1450px">
    <svg class="card-shape" width="330" height="310" viewBox="0 0 330 310" aria-hidden="true">
      <path d="M90 14Q108 4 128 4H212Q232 4 250 14L318 136Q328 155 318 174L250 296Q232 306 212 306H128Q108 306 90 296L12 174Q2 155 12 136Z" fill="#7b7b7b" opacity=".55"/>
      <path d="M82 10Q100 0 120 0H204Q224 0 242 10L310 132Q320 151 310 170L242 292Q224 302 204 302H120Q100 302 82 292L10 170Q0 151 10 132Z" fill="var(--grey-card)"/>
    </svg>
    <div class="card-body">
      <svg class="card-icon" width="54" height="48" viewBox="0 0 54 48" fill="none" stroke="#fff" stroke-width="3" aria-hidden="true"><rect x="3" y="3" width="30" height="22" rx="4"/><path d="M10 25V33L18 25"/><path d="M38 15H47Q51 15 51 19V34Q51 38 47 38H44V45L37 38H24Q20 38 20 34V30"/><path d="M12 16L17 11 22 16M17 11V20"/></svg>
      <h3>Database Management</h3>
      <p>Providing cutting edge IT Solutions that help DoD and the VA to tackle various health problems.</p>
      <span class="more">Read More</span>
      <svg class="chev" width="18" height="16" viewBox="0 0 18 16" fill="none" stroke="#fff" stroke-width="2" aria-hidden="true"><path d="M3 2L9 7 15 2M3 9L9 14 15 9"/></svg>
    </div>
  </div>
</section>

<section class="leadership">
  <h2 class="abs section-title lead-title">Leadership Team:
    <svg width="40" height="24" viewBox="0 0 40 24" fill="none" stroke="var(--teal-dark)" stroke-width="3.5" aria-hidden="true"><path d="M12 3L3 12 12 21M28 3L37 12 28 21"/></svg>
  </h2>
  <div class="abs lead-name">Ret. SFC Darnell K. Whitlow</div>
  <div class="abs lead-role">Chief Executive Office</div>
  <div class="abs lead-copy">
    <p>Pellworth &amp; Quine, LLC was founded by Retired Sergeant First Class (Ret. SFC) Darnell Whitlow. Mr. Whitlow retired from the US Army after over 20 years of service which included tours in "Operation Desert Storm/Shield", two tours of duty at the DMZ in Korea, also served in various locations in Germany including the Berlin Wall, and a Tour in Bosnia, Herzegovina for operation "Deliberate Force".</p>
    <p>Mr. Whitlow also served as a Drill Sergeant helping to mentally and physically prepare our young men for army readiness. Mr. Whitlow received accommodation (s) during his army career such as: The Army Accommodation Medal, South Asia Service Medal with 3 Bronze Stars, and the Non-Commission Officers-Professional Development Ribbon with Numeral 3, a Kuwait Liberation Medal SA, and a Combat Infantryman Badge.</p>
    <p>Mr. Whitlow provides strategic direction and lead Pellworth &amp; Quine's DOD markets.</p>
  </div>
  <div class="abs lead-quote">"Hooah"</div>
  <a class="abs btn" style="left:98px;top:2548px">Read More</a>
  <div class="abs portrait" role="img" aria-label="Portrait illustration of the chief executive"></div>
</section>

<section class="join">
  <h2 class="abs serif join-title">Join Us</h2>
  <div class="abs join-copy">
    <p>Pellworth &amp; Quine strives to provide an outstanding work environment for our employees. We invest in our people and believe strongly in creating an environment where our employees are free to work on innovative solutions that meet our clients' needs. We promote true work-life balance, career advancement, health, and financial security and fun in the work place. We encourage our employees to participate in our internal operation and help to develop them into the ideal consultants that our clients seek.</p>
    <p>Pellworth &amp; Quine, LLC is an Equal Opportunity Employer. We extend equal opportunity to all individuals without regard to race, religion, color, sex, national origin, sexual orientation, age, marital status, disability, or any other status protected without applicable law.</p>
  </div>
  <a class="abs btn btn-outline" style="left:535px;top:3048px">Read More</a>
</section>

<footer>
  <div class="abs foot-brand"><span class="mark"></span>Pellworth &amp; Quine</div>
  <nav class="abs foot-nav"><span>HOME</span><span>ABOUT</span><span>SERVICES</span><span>WHY HIRE US?</span><span>CONTACT US</span></nav>
  <div class="abs foot-rule"></div>
  <p class="abs copyright">Copyrights @ 2018 Pellworth Quine. All Rights Reserved.</p>
</footer>

</body>
</html>
```